Hip surgeon needs a educative book cover design

I need to re-design my old book cover for its 3rd edition.
It's a small book dedicated to my patients, who underwent total hip replacement. It's meant to help people getting around the basic care after a total hip replacement surgery and getting back to their normal, active life.
The title is: "Morning light rituals: a quiet companion".
I already had a new logo, new stationery and new website design from ArtFolio (please see the attachments).
The final design should be look alike the other fresh new designs. It must communicate health, peacefulness.
I also attached the manual as it looks today for reference.
A5 size.
Just cover and back cover.
Health

```html
<!DOCTYPE html>
<html lang="en">
<head>
<meta charset="utf-8">
<title>Morning Light Rituals – Cover</title>
<link rel="stylesheet" href="https://fonts.googleapis.com/css2?family=Oswald:wght@500;700&family=Roboto+Condensed:wght@700&family=Roboto:wght@300&display=swap">
<style>
  :root {
    --page-bg: #e4e4e4;
    --paper: #fbfbfc;
    --blue: #3f86cf;
    --blue-dark: #2f6fb6;
    --blue-light: #6aaee6;
    --art-light: #d9e2f4;
    --art-mid: #aab9e0;
    --art-deep: #7a8fcc;
    --white: #ffffff;
  }
  * { margin: 0; padding: 0; box-sizing: border-box; }
  html, body { width: 1200px; height: 800px; overflow: hidden; }
  body {
    background: var(--page-bg);
    display: flex; align-items: center; justify-content: center;
  }
  .cover {
    position: relative;
    width: 524px; height: 740px;
    background: var(--paper);
    overflow: hidden;
    box-shadow: 0 6px 24px rgba(0,0,0,.12);
  }
  .top-band {
    position: absolute; left: 0; top: 0; width: 100%; height: 118px;
    background: linear-gradient(90deg, var(--blue-dark), var(--blue-light));
  }
  .top-band__text {
    position: absolute; left: 22px; right: 70px; bottom: 14px;
    font: 700 12.5px/1.25 "Roboto Condensed", sans-serif;
    color: var(--white);
  }
  .hero-art {
    position: absolute; left: 0; top: 128px; width: 330px; height: 520px;
    background: radial-gradient(ellipse at 40% 45%, var(--art-light) 0%, var(--art-mid) 55%, var(--art-deep) 100%);
    border-radius: 0 40% 30% 0 / 0 30% 40% 0;
  }
  .title-box {
    position: absolute; left: 250px; top: 150px; width: 274px; height: 168px;
    background: linear-gradient(180deg, var(--blue), var(--blue-dark));
    border-radius: 16px 0 0 16px;
    padding: 18px 18px 0 22px;
    color: var(--white); text-align: center;
  }
  .title-box__main {
    font: 700 34px/1.05 "Oswald", sans-serif;
    text-transform: uppercase; letter-spacing: .5px;
  }
  .title-box__rule { height: 2px; background: var(--white); margin: 10px 0 8px; }
  .title-box__sub {
    font: 500 21px/1.1 "Oswald", sans-serif;
    text-transform: uppercase; letter-spacing: .5px;
  }
  .intro {
    position: absolute; left: 338px; top: 338px; width: 172px;
    font: 700 12.5px/1.3 "Roboto Condensed", sans-serif;
    color: var(--blue-dark); text-align: justify;
  }
  .edge-tab {
    position: absolute; right: 0; top: 458px; width: 24px; height: 38px;
    background: var(--blue);
  }
  .brand {
    position: absolute; left: 330px; top: 528px;
    display: flex; align-items: center; gap: 10px;
    color: var(--blue);
    font: 300 18px/1.15 "Roboto", sans-serif;
  }
  .brand__mark { width: 34px; height: 34px; border-radius: 50%; background: var(--blue); flex: none; }
  .brand__role { font-size: 14px; }
  .accent-bar {
    position: absolute; left: 220px; top: 578px; width: 110px; height: 30px;
    background: var(--blue);
  }
  .bottom-bar {
    position: absolute; left: 180px; top: 680px; width: 250px; height: 32px;
    background: linear-gradient(90deg, var(--blue-dark), var(--blue-light));
  }
</style>
</head>
<body>
  <main class="cover">
    <header class="top-band">
      <p class="top-band__text">Lorem ipsum dolor sit amet, consectetur adipisicing elit, sed do eiusmod tempor incididunt ut labore et dolore magna aliqua. Ut enim ad minim veniam, quis nostrud exercitation.</p>
    </header>

    <div class="hero-art" role="img" aria-label="Illustration of a hip joint with a prosthetic implant, rendered in soft blue tones"></div>

    <section class="title-box">
      <h1 class="title-box__main">Morning Light<br>Rituals</h1>
      <div class="title-box__rule"></div>
      <h2 class="title-box__sub">A Quiet Companion</h2>
    </section>

    <p class="intro">Lorem ipsum dolor sit amet, consectetur adipisicing elit, sed do eiusmod tempor incididunt ut labore et dolore magna aliqua. Ut enim ad minim veniam, quis nostrud exercitation.</p>

    <div class="edge-tab"></div>

    <div class="brand">
      <span class="brand__mark"></span>
      <div>
        <div class="brand__name">Dr. Lucas M. Arendt</div>
        <div class="brand__role">Cirurgia do Quadril</div>
      </div>
    </div>

    <div class="accent-bar"></div>
    <div class="bottom-bar"></div>
  </main>
</body>
</html>
```